Signage Design Project

Busisness is a bakery and deli long time owned by the Tavel family. Want to develop a new outside sign that communicates it is a deli and a bakery but keeps the tavel name in the design.

The sign when produced will be about 10' by 3' . It is not lighted at present but could be if it were advantageous.

The name of the store is:

Tavel's Harbor Lane Bakery and Deli. The concept is to have a new,modern sign that reinforces that it is a deli and a bakery, as most people only know about the bakery side of the business
Updates

The name Tavel is just a reinforcer so the people kno it is still in the family.  The emphasis should be on the HARBOR LANE BAKERY and DELI

Target Market(s)

Small business breakfast and lunch customers

Industry/Entity Type

Bakery

Requirements
Must have
• Great impact from the road. Communicate that it is a deli and a bakery. Keep the Tavel name but need not be a major design element

```html
<!DOCTYPE html>
<html lang="en">
<head>
<meta charset="utf-8">
<title>Tavel's Harbor Lane Bakery and Deli – Storefront Sign</title>
<link rel="stylesheet" href="https://fonts.googleapis.com/css2?family=Cormorant+SC:wght@500&display=swap">
<style>
  :root {
    --page-bg: #ffffff;
    --sign-red: #d42027;
    --lettering-white: #ffffff;
    --sign-shadow: rgba(0, 0, 0, 0.28);
  }

  html, body {
    margin: 0;
    padding: 0;
    width: 1200px;
    height: 400px;
    overflow: hidden;
    background: var(--page-bg);
  }

  .canvas {
    position: relative;
    width: 1200px;
    height: 400px;
    background: var(--page-bg);
  }

  .sign-panel {
    position: absolute;
    left: 32px;
    top: 30px;
    width: 1136px;
    height: 340px;
    background: var(--sign-red);
    box-shadow: 2px 3px 4px var(--sign-shadow);
    display: flex;
    align-items: center;
    justify-content: center;
  }

  .business-name {
    margin: 0;
    font-family: "Cormorant SC", "Times New Roman", serif;
    font-weight: 500;
    font-size: 84px;
    line-height: 1.25;
    letter-spacing: 1px;
    color: var(--lettering-white);
    text-align: center;
    white-space: nowrap;
  }

  .business-name__line {
    display: block;
  }
</style>
</head>
<body>
  <main class="canvas">
    <section class="sign-panel" aria-label="Tavel's Harbor Lane Bakery and Deli sign">
      <h1 class="business-name">
        <span class="business-name__line">Tavel's Harbor Lane</span>
        <span class="business-name__line">Bakery &amp; Deli</span>
      </h1>
    </section>
  </main>
</body>
</html>
```